Brightfen Business Card Redesign & Logo Update

We need to update our business cards to something more modern and fresh. Brightfen can provide the current color schemes and old design examples, but welcome creativity in helping us with this redesign. PLEASE NOTE that we no longer utilize the "tree" and/or "leaf" imagery in our branding. If able would apprecaite an update on the quality of our "words only" logo in Ai. / PNG formats too.

Target Market(s)

Investors, landowners, corporate partners, contractors

Industry/Entity Type

Environmental Restoration & Conservation

Contact Information for Business Card

Logo, persons name, title, mailing address, phone and email, website url

Font styles to use
Other font styles liked:
• Merriweather

Requirements
Nice to have
• Logo, persons name, title, mailing address, phone and email, website url, but open to ideams
Should not have
• No all back backgrounds

```html
<!DOCTYPE html>
<html lang="en">
<head>
<meta charset="utf-8">
<title>Brightfen Business Card</title>
<link rel="stylesheet" href="https://fonts.googleapis.com/css2?family=Open+Sans:wght@400;700&display=swap">
<style>
  :root {
    --orange: #ec7c22;
    --green: #13843f;
    --ink: #1b1b1b;
    --paper: #ffffff;
    --backdrop: #e6e8eb;
  }
  * { margin: 0; padding: 0; box-sizing: border-box; }
  html, body { width: 1200px; height: 780px; overflow: hidden; }
  body {
    background: var(--backdrop);
    font-family: "Open Sans", sans-serif;
    position: relative;
  }
  .card {
    position: absolute;
    width: 540px;
    height: 310px;
    background: var(--paper);
    overflow: hidden;
    box-shadow: 0 10px 28px rgba(0,0,0,0.18);
  }
  .card--front { left: 40px; top: 235px; }
  .card--back { left: 620px; top: 235px; }
  .card__art { position: absolute; inset: 0; width: 100%; height: 100%; }

  .brand { position: absolute; }
  .brand__name {
    display: block;
    font-family: "Open Sans", sans-serif;
    font-weight: 700;
    color: var(--green);
    line-height: 1;
  }
  .brand__line {
    display: block;
    font-family: "Open Sans", sans-serif;
    font-weight: 400;
    color: var(--ink);
    text-transform: uppercase;
    line-height: 1.2;
  }
  .card--front .brand { left: 228px; top: 34px; }
  .card--front .brand__name { font-size: 40px; letter-spacing: 1px; }
  .card--front .brand__line { font-size: 10.5px; letter-spacing: 1.6px; margin-top: 6px; }
  .card--back .brand { left: 62px; top: 62px; }
  .card--back .brand__name { font-size: 70px; letter-spacing: 2px; }
  .card--back .brand__line { font-size: 17px; letter-spacing: 3px; margin-top: 12px; }

  .person { position: absolute; left: 56px; top: 140px; }
  .person__name { font-size: 20px; font-weight: 700; line-height: 1.1; }
  .person__first { color: var(--orange); }
  .person__last { color: var(--green); }
  .person__title { font-size: 12.5px; color: var(--ink); margin-top: 4px; }

  .divider {
    position: absolute;
    left: 246px; top: 138px;
    width: 1.5px; height: 82px;
    background: var(--ink);
  }
  .contact { position: absolute; left: 262px; top: 138px; list-style: none; }
  .contact__item {
    display: flex; align-items: center;
    font-size: 13px; color: var(--ink);
    height: 21px;
  }
  .contact__icon { width: 14px; height: 14px; margin-right: 8px; flex: none; }
</style>
</head>
<body>

<section class="card card--back" aria-label="Card back">
  <svg class="card__art" viewBox="0 0 540 310" preserveAspectRatio="none">
    <rect x="0" y="226" width="540" height="84" fill="var(--orange)"/>
    <rect x="0" y="214" width="540" height="3" fill="var(--green)"/>
  </svg>
  <div class="brand">
    <span class="brand__name">BRIGHTFEN</span>
    <span class="brand__line">Restoration &amp; Conservation</span>
  </div>
</section>

<section class="card card--front" aria-label="Card front">
  <svg class="card__art" viewBox="0 0 540 310" preserveAspectRatio="none">
    <path d="M0,150 C40,250 250,300 540,282 L540,310 L0,310 Z" fill="var(--orange)"/>
    <path d="M14,128 C60,240 260,290 480,274" fill="none" stroke="var(--green)" stroke-width="2.5"/>
  </svg>

  <div class="brand">
    <span class="brand__name">BRIGHTFEN</span>
    <span class="brand__line">Restoration &amp; Conservation</span>
  </div>

  <div class="person">
    <p class="person__name"><span class="person__first">Marta</span> <span class="person__last">Kovalenko</span></p>
    <p class="person__title">Managing Director</p>
  </div>

  <div class="divider"></div>

  <ul class="contact">
    <li class="contact__item">
      <svg class="contact__icon" viewBox="0 0 16 16"><path d="M4 1.5 L6.5 4.5 L5 6.2 C6 8.3 7.7 10 9.8 11 L11.5 9.5 L14.5 12 L12.8 14.3 C7 14 2 9 1.7 3.2 Z" fill="var(--orange)"/></svg>
      (555) 014-2290
    </li>
    <li class="contact__item">
      <svg class="contact__icon" viewBox="0 0 16 16"><rect x="4" y="1" width="8" height="14" rx="1.5" fill="var(--orange)"/><rect x="5.5" y="3" width="5" height="8" fill="#fff"/><circle cx="8" cy="13" r="0.9" fill="#fff"/></svg>
      (555) 014-2290
    </li>
    <li class="contact__item">
      <svg class="contact__icon" viewBox="0 0 16 16"><rect x="1" y="3" width="14" height="10" rx="1" fill="var(--orange)"/><path d="M1.5 3.8 L8 9 L14.5 3.8" fill="none" stroke="#fff" stroke-width="1.3"/></svg>
      info@brightfen.com
    </li>
    <li class="contact__item">
      <svg class="contact__icon" viewBox="0 0 16 16"><circle cx="8" cy="8" r="7" fill="var(--orange)"/><ellipse cx="8" cy="8" rx="3" ry="7" fill="none" stroke="#fff" stroke-width="1"/><path d="M1 8 H15 M2.5 4.5 H13.5 M2.5 11.5 H13.5" stroke="#fff" stroke-width="1"/></svg>
      www.brightfen.com
    </li>
  </ul>
</section>

</body>
</html>
```